Harborview Estates Business Card for Apartment Buildings

Create business cards for resident managers who run apartment buildings. The audience is the public who are searching for apartment rentals, and current residents who live at the apartment building. Key design element will be incorporating the company logo, however, the logo cannot dominate. The building name and manager name are more important than the logo. Current business card design leaves little room for copy, so we may need to reduce the size on the current card to allow for more space for copy.

Target Market(s)

Adults 18-65 years of age, who are looking for an apartment rental, plus current residents who live at our apartment buildings.

Industry/Entity Type

Property Management

Contact Information for Business Card

A major design element will be use of the company logo. Important property and manager contact information must be part of the design. The size of the logo will need to be reduced to make room for building and manager contact copy.

Font styles to use
Sans Serif

Colors
3176b5
000000
959595
ffffff

Requirements
Must have
• 1) Incorporate the company logo.
• 2) Use the company colors (dark blue, black/grey, over white).
• 3) FEATURE THE BUILDING NAME
• 4) FEATURE THE MANAGER NAME
• 5) The company name is less important than BUILDING and MANAGER
• 6) Manager contact information
• **SEE ATTACHED CREATIVE BRIEF**
Nice to have
• 1) Back of card logo watermark
• 2) Ability to write notes on back of carfd
Should not have
• Avoid letting the company logo dominate the card, the building name and manager are more important than the company logo.

```html
<!DOCTYPE html>
<html lang="en">
<head>
<meta charset="utf-8">
<title>Harborview Estates Business Card</title>
<link href="https://fonts.googleapis.com/css2?family=Roboto:wght@400;500;700;900&display=swap" rel="stylesheet">
<style>
  :root {
    --brand-blue: #0f5a9c;
    --accent-blue: #3176b5;
    --ink: #1a1a1a;
    --grey: #959595;
    --paper: #ffffff;
    --backdrop: #e4e6ea;
    --watermark: #eceef2;
  }
  * { box-sizing: border-box; margin: 0; padding: 0; }
  html, body { width: 1200px; height: 800px; overflow: hidden; }
  body {
    background: var(--backdrop);
    font-family: "Roboto", Arial, sans-serif;
    position: relative;
  }
  .card {
    position: absolute;
    width: 600px;
    height: 343px;
    background: var(--paper);
    box-shadow: 0 8px 24px rgba(0,0,0,.18);
    overflow: hidden;
  }
  .card--front { left: 120px; top: 40px; }
  .card--back { left: 480px; top: 417px; }

  .front-band { position: absolute; inset: 0; }

  .brand { position: absolute; left: 52px; top: 42px; display: flex; align-items: center; gap: 16px; }
  .brand-mark {
    width: 96px; height: 96px; border-radius: 50%;
    background: var(--paper);
    border: 6px solid var(--ink);
    flex: none;
  }
  .brand-name {
    color: var(--brand-blue);
    font-weight: 900;
    font-size: 36px;
    line-height: 1;
    letter-spacing: .5px;
    text-transform: uppercase;
  }
  .brand-name span { display: block; font-size: 17px; letter-spacing: 5px; margin-top: 6px; }

  .address {
    position: absolute; right: 26px; top: 138px;
    text-align: right; font-size: 13px; line-height: 1.35; color: var(--ink);
  }
  .address .web { color: var(--accent-blue); }

  .divider {
    position: absolute; left: 186px; right: 22px; top: 200px;
    height: 2px; background: var(--accent-blue);
  }

  .manager { position: absolute; left: 196px; top: 212px; }
  .manager-name {
    color: var(--brand-blue); font-weight: 700; font-size: 20px;
    text-transform: uppercase; line-height: 1.1;
  }
  .manager-title { font-size: 14px; color: var(--ink); margin-top: 2px; }
  .contacts { list-style: none; margin-top: 12px; font-size: 13.5px; color: var(--ink); }
  .contacts li { display: flex; align-items: center; gap: 8px; line-height: 1.5; }
  .contacts svg { width: 12px; height: 12px; fill: var(--brand-blue); flex: none; }

  .watermark { position: absolute; left: 150px; top: 40px; display: flex; align-items: center; gap: 24px; }
  .watermark-mark {
    width: 250px; height: 250px; border-radius: 50%;
    border: 14px solid var(--watermark);
  }
  .watermark-name {
    position: absolute; left: 50%; top: 50%; transform: translate(-50%,-50%);
    color: var(--watermark); font-weight: 900; font-size: 30px;
    text-transform: uppercase; white-space: nowrap;
  }
</style>
</head>
<body>
  <section class="card card--front" aria-label="Business card front">
    <svg class="front-band" width="600" height="343" viewBox="0 0 600 343" aria-hidden="true">
      <polygon points="0,0 82,0 165,343 0,343" fill="var(--brand-blue)"/>
      <line x1="96" y1="0" x2="179" y2="343" stroke="var(--ink)" stroke-width="3"/>
    </svg>

    <div class="brand">
      <div class="brand-mark"></div>
      <div class="brand-name">Harborview<span>Estates LLC</span></div>
    </div>

    <div class="address">
      2750 Linden Grove Road #B210<br>
      Fairhaven, CA 94870<br>
      <span class="web">www.harborviewestates.us</span>
    </div>

    <div class="divider"></div>

    <div class="manager">
      <div class="manager-name">Dana Whitfield</div>
      <div class="manager-title">Property Manager</div>
      <ul class="contacts">
        <li><svg viewBox="0 0 24 24"><path d="M6.6 10.8a15 15 0 0 0 6.6 6.6l2.2-2.2a1 1 0 0 1 1-.25 11.4 11.4 0 0 0 3.6.57 1 1 0 0 1 1 1V20a1 1 0 0 1-1 1A17 17 0 0 1 3 4a1 1 0 0 1 1-1h3.5a1 1 0 0 1 1 1c0 1.25.2 2.45.57 3.57a1 1 0 0 1-.25 1z"/></svg>555-014-2231</li>
        <li><svg viewBox="0 0 24 24"><path d="M7 2h10a2 2 0 0 1 2 2v16a2 2 0 0 1-2 2H7a2 2 0 0 1-2-2V4a2 2 0 0 1 2-2zm0 3v13h10V5z"/></svg>555-014-7788</li>
        <li><svg viewBox="0 0 24 24"><path d="M2 5h20v14H2zm2 2v.5l8 5 8-5V7l-8 5z"/></svg>dana@harborviewestates.us</li>
      </ul>
    </div>
  </section>

  <section class="card card--back" aria-label="Business card back">
    <div class="watermark">
      <div class="watermark-mark"></div>
    </div>
    <div class="watermark-name">Harborview Estates</div>
  </section>
</body>
</html>
```